Tovel & Associates - London New Letting and Property Management Company *

Tovel & Associates LTD is a new company based in London, and works with brand new residential property in the city centre.

We are aiming to have 1000 new properties a year.

We are looking for something modern and minimalistic :
Logo ,Monogram, Paper Head and Business Card.

Target Market(s)

Internation landlords

Industry/Entity Type

Real Estate

Logo Text

Tovel & Associates

Colors

Designer to choose colors to be used in the design.

Requirements
Nice to have
• A particular monogram with "TA"
Should not have
• Little House over the logo

```html
<!DOCTYPE html>
<html lang="en">
<head>
<meta charset="utf-8">
<title>Tovel &amp; Associates LTD – Business Card</title>
<link rel="stylesheet" href="https://fonts.googleapis.com/css2?family=Montserrat:wght@600;700&family=Open+Sans:wght@400;600&display=swap">
<style>
  :root {
    --stage: #161616;
    --card: #262626;
    --card-edge: #2e2e2e;
    --blue: #1a7bc4;
    --white: #f4f4f4;
    --foil: #9c9c9c;
  }
  * { box-sizing: border-box; margin: 0; padding: 0; }
  html, body { width: 1200px; height: 900px; overflow: hidden; background: var(--stage); }
  .stage {
    width: 1200px; height: 900px;
    display: flex; flex-direction: column; align-items: center; justify-content: center;
    gap: 40px;
  }
  .card {
    width: 700px; height: 400px;
    background: var(--card);
    border: 1px solid var(--card-edge);
    position: relative;
  }
  .card-front { display: flex; align-items: center; justify-content: center; }
  .brand {
    display: flex; align-items: center; gap: 14px;
    font-family: "Montserrat", sans-serif; font-weight: 700;
  }
  .brand-mark { width: 22px; height: 22px; }
  .card-front .brand { font-size: 34px; color: var(--foil); }
  .card-front .brand-mark { background: var(--foil); width: 26px; height: 26px; }
  .card-back { display: flex; align-items: center; }
  .back-brand {
    width: 340px; display: flex; justify-content: center;
  }
  .card-back .brand { font-size: 25px; color: var(--white); flex-direction: column; align-items: flex-start; gap: 10px; }
  .card-back .brand-mark { background: var(--blue); }
  .divider { width: 3px; height: 230px; background: var(--blue); }
  .details { padding-left: 40px; font-family: "Open Sans", sans-serif; color: var(--white); }
  .person-name {
    font-family: "Montserrat", sans-serif; font-weight: 700;
    font-size: 24px; color: var(--blue); letter-spacing: 0.5px;
  }
  .person-role { font-size: 17px; margin-bottom: 16px; }
  .contact-list { list-style: none; font-size: 17px; line-height: 1.45; }
  .contact-list li { display: flex; align-items: center; gap: 12px; }
  .contact-list svg { width: 14px; height: 14px; flex: none; }
  .web-domain { color: var(--blue); }
  .address { margin-top: 14px; font-size: 18px; line-height: 1.4; }
</style>
</head>
<body>
<main class="stage">
  <section class="card card-front" aria-label="Card front">
    <div class="brand">
      <span class="brand-mark"></span>
      <span class="brand-name">Tovel &amp; Associates LTD</span>
    </div>
  </section>

  <section class="card card-back" aria-label="Card back">
    <div class="back-brand">
      <div class="brand">
        <span class="brand-mark"></span>
        <span class="brand-name">Tovel &amp; Associates LTD</span>
      </div>
    </div>
    <div class="divider"></div>
    <div class="details">
      <p class="person-name">ELIN HARROW</p>
      <p class="person-role">Founder</p>
      <ul class="contact-list">
        <li>
          <svg viewBox="0 0 14 14" fill="none" stroke="#1a7bc4" stroke-width="1.4"><rect x="3.5" y="0.8" width="7" height="12.4" rx="1.2"/><line x1="6" y1="11" x2="8" y2="11"/></svg>
          020. 7946. 0321
        </li>
        <li>
          <svg viewBox="0 0 14 14" fill="#1a7bc4"><path d="M3 1l2.2 2.6-1.2 1.6c.8 1.8 2.2 3.3 4 4.2l1.5-1.2L12 10.5 10.6 13C5.5 12.3 1.7 8.4 1 3.3z"/></svg>
          020. 7946. 0588
        </li>
        <li>
          <svg viewBox="0 0 14 14" fill="none" stroke="#1a7bc4" stroke-width="1.3"><rect x="1" y="3" width="12" height="8.5"/><polyline points="1,3 7,8 13,3"/></svg>
          info@tovelassociates.com
        </li>
        <li>
          <svg viewBox="0 0 14 14" fill="none" stroke="#1a7bc4" stroke-width="1.2"><circle cx="7" cy="7" r="6"/><ellipse cx="7" cy="7" rx="2.6" ry="6"/><line x1="1" y1="7" x2="13" y2="7"/></svg>
          <span>www.<span class="web-domain">tovelassociates</span>.com</span>
        </li>
      </ul>
      <p class="address">48 Carrow Lane<br>London, EC2A 4PX</p>
    </div>
  </section>
</main>
</body>
</html>
```